Brambleton Pizza Website

We are working with Brambleton Pizza and designing them a website.

Some sites to use for content/competitors and inspiration:

https://fennimores.com
https://www.bhq-eats.com
https://brightorchard.com/en-us/

Thank you for taking the time to consider designing a website for us. We are web developers based in Stockton, CA, USA. Most of our projects go through the same process. Understanding this process may help you win a project with us. We custom-code all of our websites in-house. We don’t have any requirements as to what tools you use for your design, but we prefer Figma files. For any design that we label as four-stars, we send it to the client for review. The client picks the final design they want us to use. Once we complete this process, we will continue to show additional clients all the four-star sites and purchase them later. Your designs will have multiple chances to sell. For better chances of success, we ask that you follow these guidelines.

IMAGES:
If you use any images or icons in the design, we ask that you have a link to the asset so we can purchase the image/icon. Most of the designs we submit do not have the customer’s images on them unless they have some great images. Be creative; show us the feeling you are trying to portray with your image choices. Use any royalty-free site you choose. We subscribe to Quillstone and mainly use their images, but we can purchase images outside of Quillstone.

PLEASE NOTE: we will not submit designs to clients with watermarks on the images.

FONTS:
We ask that you identify the fonts used in the design. This can be done in a message if you want. We typically use Google Fonts and Quillstone Fonts.

CONTENT:
We're always open to different content and ideas. We often submit designs with stock images so the client can see our vision. We typically take pictures after the website launch to use their images with our vision. Lorem Ipsum is fine for paragraphs, but we ask that you write the headers in correct English. We want to be able to show the vision and identify the sections of the website.

INSPIRATION:
We typically add a couple of links in the brief of websites we like to help you get started in your design.

REVISIONS:
We do not often ask for revisions of the designs unless we see something in the design that may not appeal to the client. If there are slight changes that we want to make, we do that in the development process.

FEEDBACK:
We rarely give feedback on designs during the design process. We are working on many website projects and do not have the time to provide feedback. We usually respond if your request is well thought out and asks specific questions, but a note asking “feedback, please” usually goes unanswered.

```html
<!DOCTYPE html>
<html lang="en">
<head>
<meta charset="utf-8">
<title>Brambleton Pizza</title>
<link href="https://fonts.googleapis.com/css2?family=Oswald:wght@500;600;700&family=Poppins:wght@400;500;600&display=swap" rel="stylesheet">
<style>
:root{
  --red:#e2231a;
  --red-dark:#b3140e;
  --green:#2f9e44;
  --green-dark:#1f7a31;
  --ink:#1d1d1d;
  --muted:#6a6a6a;
  --white:#ffffff;
  --head:'Oswald',sans-serif;
  --body:'Poppins',sans-serif;
}
*{box-sizing:border-box;margin:0;padding:0}
html,body{width:1200px;height:3792px;overflow:hidden}
body{position:relative;background:var(--white);font-family:var(--body);color:var(--ink)}
.abs{position:absolute}
.backdrop{position:absolute;left:0;top:0;z-index:0}
.photo{position:absolute}
.brand{position:absolute;z-index:6;font-family:var(--head);font-weight:700;color:var(--white);font-size:30px;line-height:1.05;text-transform:uppercase;display:flex;align-items:center;gap:12px}
.brand-dot{width:16px;height:16px;border-radius:50%;background:var(--white)}
.header-bar{position:absolute;z-index:5;left:350px;top:0;width:850px;height:70px;background:var(--white);border-bottom-left-radius:34px}
.nav{position:absolute;z-index:6;top:26px;left:390px;display:flex;gap:36px;font-size:14px;font-weight:500}
.nav a{color:var(--ink);text-decoration:none}
.nav a.active{color:var(--red);border-bottom:2px solid var(--red);padding-bottom:6px}
.nav-icons{position:absolute;z-index:6;top:22px;left:960px;display:flex;gap:28px}
.btn{display:inline-block;background:var(--green);color:var(--white);font-family:var(--body);font-weight:600;font-size:14px;padding:14px 32px;text-transform:uppercase;text-decoration:none;clip-path:polygon(0 0,100% 0,90% 100%,0 100%);z-index:4}
.btn.red{background:var(--red)}
.hero-title{position:absolute;z-index:3;left:110px;top:196px;width:480px;font-family:var(--head);font-weight:700;font-size:46px;line-height:1.18;color:var(--white)}
.hero-copy{position:absolute;z-index:3;left:110px;top:378px;width:440px;font-size:15px;line-height:1.5;color:#fff6d8}
.section-title{position:absolute;z-index:3;width:100%;text-align:center;font-family:var(--head);font-weight:700;font-size:44px;color:var(--ink)}
.menu-list{position:absolute;z-index:3;left:580px;top:780px;width:510px;list-style:none}
.menu-list li{display:flex;justify-content:space-between;align-items:center;height:39px;color:var(--white);font-weight:600;font-size:15px;padding:0 10px;border-bottom:2px solid rgba(255,255,255,.85)}
.delivery-photo{left:690px;top:1200px;width:410px;height:440px;border-radius:24px;z-index:2}
.delivery-card{position:absolute;z-index:3;left:222px;top:1268px;width:540px;height:330px;background:var(--white);border:5px solid var(--green);border-left-color:var(--red);border-top-color:var(--red);border-radius:14px;padding:40px 40px;box-shadow:0 10px 30px rgba(0,0,0,.12)}
.delivery-card .row{display:flex;align-items:center;gap:18px}
.delivery-card h3{font-family:var(--head);font-weight:700;font-size:38px}
.delivery-card p{font-size:14px;line-height:1.6;width:300px;margin:20px 0 34px;color:var(--muted)}
.offers{position:absolute;z-index:3;left:112px;top:1780px;display:flex;gap:14px}
.offer{width:232px;height:400px;background:var(--white);border:2px solid var(--green);border-top-color:var(--red);border-radius:12px;padding:6px;text-align:center;box-shadow:0 6px 18px rgba(0,0,0,.1)}
.offer .photo{position:relative;height:200px;border-radius:8px}
.offer h4{font-family:var(--body);font-weight:600;font-size:16px;margin-top:14px}
.offer .tag{font-size:12px;color:var(--muted);margin-top:4px}
.offer .rating{display:flex;justify-content:center;gap:8px;align-items:center;font-size:11px;color:var(--muted);margin-top:8px}
.stars{color:#f2b01e;letter-spacing:1px;font-size:13px}
.offer .price{color:var(--red);font-weight:600;font-size:16px;margin:6px 0 14px}
.arrow{position:absolute;z-index:3;top:1964px;width:48px;height:48px;border-radius:50%;border:3px solid var(--red);background:var(--white);display:flex;align-items:center;justify-content:center}
.arrow.left{border-color:#8a8a8a}
.follow-title{position:absolute;z-index:3;top:2396px;width:100%;text-align:center;font-family:var(--head);font-weight:700;font-size:44px;color:var(--ink);display:flex;justify-content:center;align-items:center;gap:14px}
.follow-mark{width:36px;height:36px;border:4px solid var(--ink);border-radius:10px}
.gallery{position:absolute;z-index:3;left:112px;top:2488px;display:flex;gap:14px}
.gallery .photo{position:relative;width:232px;height:300px;border-radius:22px}
.closing-title{position:absolute;z-index:3;left:110px;top:3000px;width:540px;font-family:var(--head);font-weight:700;font-size:42px;line-height:1.22;color:var(--ink)}
.footer-col{position:absolute;z-index:3;top:3490px}
.footer-col h5{font-family:var(--head);font-weight:700;font-size:22px;letter-spacing:.5px;margin-bottom:14px}
.footer-col ul{list-style:none}
.footer-col li{font-size:14px;margin-bottom:10px;display:flex;align-items:center;gap:10px}
.footer-col li::before{content:"";width:7px;height:7px;border-top:2px solid var(--ink);border-right:2px solid var(--ink);transform:rotate(45deg)}
.footer-col.contact li::before{display:none}
.icon-dot{width:34px;height:34px;border-radius:50%;background:var(--red);display:flex;align-items:center;justify-content:center}
.legal{position:absolute;z-index:3;top:3756px;left:110px;font-size:12px;color:var(--ink)}
.pay{position:absolute;z-index:3;top:3752px;left:700px;display:flex;gap:6px}
.pay span{width:38px;height:22px;background:var(--white);border:1px solid #cfcfcf;border-radius:4px}
</style>
</head>
<body>

<svg class="backdrop" width="1200" height="3792" viewBox="0 0 1200 3792" aria-hidden="true">
  <defs>
    <linearGradient id="followBand" x1="0" y1="0" x2="1" y2="0">
      <stop offset="0" stop-color="#d92c1f"/><stop offset=".5" stop-color="#c8a08a"/><stop offset="1" stop-color="#2f9e44"/>
    </linearGradient>
    <linearGradient id="footBand" x1="0" y1="0" x2="1" y2="1">
      <stop offset="0" stop-color="#f2b5ad"/><stop offset=".55" stop-color="#f3f0ee"/><stop offset="1" stop-color="#a9d9b1"/>
    </linearGradient>
  </defs>
  <rect x="0" y="0" width="620" height="660" fill="var(--red)"/>
  <path d="M0 640 C300 610 800 590 1200 600 L1200 1200 C950 1205 700 1190 480 1150 C300 1110 140 1070 0 1030Z" fill="var(--green)"/>
  <path d="M0 610 C200 680 450 690 620 620 L620 660 L0 660Z" fill="var(--white)"/>
  <path d="M0 1030 C180 1090 380 1150 620 1190 C420 1250 200 1300 0 1340Z" fill="var(--red)"/>
  <path d="M900 1200 C1050 1215 1150 1250 1200 1290 L1200 1200Z" fill="var(--red)"/>
  <path d="M0 1520 C220 1620 520 1640 780 1590 L780 1610 C520 1670 220 1660 0 1580Z" fill="var(--green)"/>
  <path d="M0 2300 C300 2220 800 2300 1200 2250 L1200 2900 C900 2850 400 2900 0 2860Z" fill="url(#followBand)"/>
  <path d="M0 2240 C400 2360 800 2260 1200 2340 L1200 2250 C800 2300 300 2220 0 2300Z" fill="var(--white)"/>
  <path d="M0 3400 C400 3460 800 3440 1200 3400 L1200 3792 L0 3792Z" fill="url(#footBand)"/>
</svg>

<!-- header -->
<div class="brand" style="left:100px;top:28px"><span class="brand-dot"></span>Brambleton<br>Pizza</div>
<div class="header-bar"></div>
<nav class="nav">
  <a class="active" href="#">HOME</a><a href="#">ABOUT US</a><a href="#">OUR MENU</a><a href="#">FRANCHISE</a><a href="#">CONTACT US</a>
</nav>
<div class="nav-icons">
  <svg width="22" height="22" viewBox="0 0 22 22"><circle cx="9" cy="9" r="7" fill="none" stroke="var(--ink)" stroke-width="2.5"/><line x1="14" y1="14" x2="20" y2="20" stroke="var(--ink)" stroke-width="2.5"/></svg>
  <svg width="22" height="22" viewBox="0 0 22 22"><circle cx="11" cy="7" r="5" fill="none" stroke="var(--ink)" stroke-width="2"/><path d="M2 21c1-6 17-6 18 0" fill="none" stroke="var(--ink)" stroke-width="2"/></svg>
  <svg width="24" height="22" viewBox="0 0 24 22"><path d="M1 2h4l3 12h12l3-9H7" fill="none" stroke="var(--ink)" stroke-width="2"/><circle cx="10" cy="19" r="2" fill="var(--ink)"/><circle cx="18" cy="19" r="2" fill="var(--ink)"/></svg>
</div>

<!-- hero -->
<div class="photo" role="img" aria-label="Pepperoni pizza with a slice lifted and cheese stretching, on a dark background" style="left:600px;top:0;width:600px;height:610px;z-index:1;background:radial-gradient(circle at 60% 55%,#c8552b 0,#8a2d14 30%,#2a1a14 60%,#151010 100%)"></div>
<h1 class="hero-title">Slice into Happiness – Fresh, Hot, and Delicious Every Time!</h1>
<p class="hero-copy">Lorem Ipsum is simply dummy text of the printing and typesetting industry. Lorem Ipsum has been the industry's</p>
<a class="btn abs" href="#" style="left:110px;top:458px">Order Now</a>

<!-- menu -->
<h2 class="section-title" style="top:700px;left:0">Our Menu</h2>
<div class="photo" role="img" aria-label="Plate of penne pasta in tomato sauce with basil" style="z-index:2;left:160px;top:820px;width:300px;height:300px;border-radius:50%;border:6px solid var(--white);background:radial-gradient(circle,#e0642c 0,#c43a1a 55%,#f5efe6 70%)"></div>
<ul class="menu-list">
  <li><span>Seafood Pasta</span><span>HK$ 109</span></li>
  <li><span>Pepperoni</span><span>HK$ 59</span></li>
  <li><span>Classic Margherita</span><span>HK$ 109</span></li>
  <li><span>Seafood Classic</span><span>HK$ 59</span></li>
  <li><span>Chicken &amp; Bacon</span><span>HK$ 59</span></li>
  <li><span>Tomato And Pesto</span><span>HK$ 59</span></li>
  <li><span>Ham &amp; Mushroom</span><span>HK$ 59</span></li>
  <li><span>The Veggie One</span><span>HK$ 59</span></li>
  <li><span>Pasta Carbonara</span><span>HK$ 59</span></li>
</ul>

<!-- delivery -->
<div class="photo delivery-photo" role="img" aria-label="Smartphone with delivery app beside a red delivery scooter carrying a pizza box" style="background:linear-gradient(135deg,#3fb95a 0,#e8e8e8 45%,#d9281e 100%)"></div>
<div class="delivery-card">
  <div class="row">
    <h3>Delivery in 1 Hour</h3>
    <svg width="30" height="30" viewBox="0 0 30 30"><circle cx="15" cy="15" r="14" fill="var(--green)"/><path d="M8 15l5 5 9-10" fill="none" stroke="#fff" stroke-width="3"/></svg>
  </div>
  <p>We Offer a Full Refund via Store Credits for All late Deliveries</p>
  <a class="btn red" href="#">Order Now</a>
</div>

<!-- offers -->
<h2 class="section-title" style="top:1700px;left:0">Special Offers</h2>
<div class="arrow left" style="left:24px"><svg width="18" height="18" viewBox="0 0 18 18"><path d="M12 2L5 9l7 7" fill="none" stroke="#8a8a8a" stroke-width="3"/></svg></div>
<div class="arrow" style="left:1128px"><svg width="18" height="18" viewBox="0 0 18 18"><path d="M6 2l7 7-7 7" fill="none" stroke="var(--red)" stroke-width="3"/></svg></div>
<div class="offers">
  <div class="offer"><div class="photo" role="img" aria-label="Vegetable pizza on a board" style="background:linear-gradient(135deg,#6b4a2e,#c9743a)"></div><h4>The Veggie One</h4><div class="tag">Limited Time Offers</div><div class="rating"><span class="stars">★★★★★</span>5271 Reviews</div><div class="price">HK$ 59</div><a class="btn red" href="#">Order Now</a></div>
  <div class="offer"><div class="photo" role="img" aria-label="Bowl of pasta carbonara" style="background:linear-gradient(135deg,#d8b78a,#c0512a)"></div><h4>Pasta Carbonara</h4><div class="tag">Limited Time Offers</div><div class="rating"><span class="stars">★★★★★</span>5271 Reviews</div><div class="price">HK$ 59</div><a class="btn red" href="#">Order Now</a></div>
  <div class="offer"><div class="photo" role="img" aria-label="Seafood pizza with herbs" style="background:linear-gradient(135deg,#4b5a3a,#b08a5a)"></div><h4>Seafood Pasta</h4><div class="tag">Limited Time Offers</div><div class="rating"><span class="stars">★★★★★</span>5271 Reviews</div><div class="price">HK$ 109</div><a class="btn red" href="#">Order Now</a></div>
  <div class="offer"><div class="photo" role="img" aria-label="Classic margherita pizza slices" style="background:linear-gradient(135deg,#d7c7a8,#8a6a46)"></div><h4>Classic Margherita</h4><div class="tag">Limited Time Offers</div><div class="rating"><span class="stars">★★★★★</span>5271 Reviews</div><div class="price">HK$ 59</div><a class="btn red" href="#">Order Now</a></div>
</div>

<!-- follow -->
<h2 class="follow-title">Follow Us On <span class="follow-mark"></span></h2>
<div class="gallery">
  <div class="photo" role="img" aria-label="Pepperoni pizza close-up" style="background:linear-gradient(135deg,#b8422a,#e0a060)"></div>
  <div class="photo" role="img" aria-label="Pizza and pasta dishes on a table" style="background:linear-gradient(135deg,#7a8a5a,#d8b88a)"></div>
  <div class="photo" role="img" aria-label="Glass of red drink with pizza behind" style="background:linear-gradient(135deg,#e0331f,#f08060)"></div>
  <div class="photo" role="img" aria-label="Sliced pizza on a wooden board" style="background:linear-gradient(135deg,#5a3a24,#c98a4a)"></div>
</div>
<a class="btn red abs" href="#" style="left:530px;top:2836px">View More</a>

<!-- closing -->
<h2 class="closing-title">Hot, Fresh, and Delivered Right to Your Door – Pizza Perfection in Every Bite!</h2>
<a class="btn red abs" href="#" style="left:110px;top:3200px">Order Now</a>
<div class="photo" role="img" aria-label="Whole sliced pepperoni pizza seen from above" style="z-index:2;left:664px;top:2920px;width:410px;height:410px;border-radius:50%;border:6px solid var(--white);box-shadow:0 0 0 4px var(--green);background:radial-gradient(circle,#d9662e 0,#b5401c 50%,#2a1d18 72%)"></div>

<!-- footer -->
<div class="brand" style="left:110px;top:3540px;color:var(--ink);font-size:34px"><span class="brand-dot" style="background:var(--red)"></span>Brambleton<br>Pizza</div>
<div class="footer-col" style="left:432px"><h5>QUICK LINKS</h5><ul><li>Home</li><li>About Us</li><li>Our Menu</li><li>Franchise</li></ul></div>
<div class="footer-col" style="left:660px"><h5>HELP LINKS</h5><ul><li>Contact Us</li><li>Terms of Use</li><li>Privacy Policy</li><li>Support Links</li><li>Conditions</li></ul></div>
<div class="footer-col contact" style="left:872px"><h5>CONTACT US</h5><ul>
  <li><span class="icon-dot"><svg width="16" height="16" viewBox="0 0 16 16"><path d="M3 1l3 3-2 2c1 3 3 5 6 6l2-2 3 3-2 2C7 15 1 9 1 3z" fill="#fff"/></svg></span>000-000-0000</li>
  <li><span class="icon-dot"><svg width="16" height="16" viewBox="0 0 16 16"><rect x="1" y="3" width="14" height="10" fill="none" stroke="#fff" stroke-width="1.6"/><path d="M1 3l7 6 7-6" fill="none" stroke="#fff" stroke-width="1.6"/></svg></span>info@brambletonpizza.com</li>
</ul></div>
<p class="legal">Copyright©2025 Brambleton Pizza. All Rights Reserved</p>
<div class="pay"><span></span><span></span><span></span><span></span><span></span><span></span><span></span><span></span></div>

</body>
</html>
```